Brightwave Reach - Business Card

We need a business card for a Social Media Marketing company that specializes in online marketing for small businesses in Canada using common Social Media platforms such as Pixlora, Chatterly, Blinkpost & Quibber.

I have uploaded a copy of our logo which I would like utilized in the business card. We would like the business card to be modern yet classy design.

Our website is www.brightwavereach.ca

Industry/Entity Type

Marketing

Contact Information for Business Card

Email: info@brightwavereach.ca
Website: www.brightwavereach.ca
Telephone: 604-555-0193

Colors

Designer to choose colors to be used in the design.

Requirements
Must have
• Social Media icons on reverse
• Please add some designs with color.

```html
<!DOCTYPE html>
<html lang="en">
<head>
<meta charset="utf-8">
<title>Brightwave Reach - Business Card</title>
<link href="https://fonts.googleapis.com/css2?family=Open+Sans:wght@400;600;700&family=Oswald:wght@700&display=swap" rel="stylesheet">
<style>
  :root {
    --backdrop: #2b2b2d;
    --card: #f3f3f3;
    --ink: #3a3d3e;
    --ink-soft: #8a8c8e;
    --art-dark: #33393a;
    --art-mid: #4a5153;
    --accent: #b3322e;
  }
  * { margin: 0; padding: 0; box-sizing: border-box; }
  html, body {
    width: 1200px; height: 840px; overflow: hidden;
    background: var(--backdrop);
  }
  .canvas {
    position: relative; width: 1200px; height: 840px;
    display: flex; align-items: center; justify-content: center; gap: 60px;
  }
  .card {
    background: var(--card);
    box-shadow: 0 10px 30px rgba(0,0,0,.45);
    position: relative;
    overflow: hidden;
  }

  /* Front */
  .card--front {
    width: 620px; height: 354px;
    display: flex; align-items: center; justify-content: center;
  }
  .brand {
    display: flex; align-items: center; gap: 16px;
    font-family: "Oswald", sans-serif; font-weight: 700;
    font-size: 38px; line-height: 1.02; letter-spacing: 1px;
    text-transform: uppercase; color: var(--ink);
  }
  .brand__square {
    width: 30px; height: 30px; background: var(--accent);
  }
  .brand__name { display: block; }

  /* Back */
  .card--back {
    width: 354px; height: 620px;
    font-family: "Open Sans", sans-serif;
    color: var(--ink);
  }
  .contact {
    position: absolute; left: 44px; top: 60px; right: 30px;
  }
  .contact__name {
    font-weight: 700; font-size: 17px; letter-spacing: .5px; text-transform: uppercase;
  }
  .contact__role {
    font-size: 13px; color: var(--accent); text-transform: uppercase;
    letter-spacing: .5px; margin-bottom: 14px;
  }
  .contact__line { font-size: 14px; line-height: 1.6; }
  .socials { display: flex; gap: 12px; margin-top: 10px; list-style: none; }
  .socials__item {
    display: flex; align-items: center; gap: 4px;
    font-size: 10px; font-weight: 600; color: var(--ink);
  }
  .socials__dot {
    width: 14px; height: 14px; border-radius: 50%; border: 1.5px solid var(--ink);
  }
  .leaf-art {
    position: absolute; left: 40px; right: 0; bottom: 0;
    height: 290px;
    background: linear-gradient(150deg, var(--art-mid) 0%, var(--art-dark) 60%, #5a2a28 100%);
  }
  .leaf-art__stripe {
    position: absolute; left: 0; top: 0; width: 100%; height: 6px;
    background: var(--accent);
  }
</style>
</head>
<body>
<main class="canvas">
  <section class="card card--front" aria-label="Card front">
    <div class="brand">
      <span class="brand__square" aria-hidden="true"></span>
      <span class="brand__name">Brightwave<br>Reach</span>
    </div>
  </section>

  <section class="card card--back" aria-label="Card back">
    <div class="contact">
      <p class="contact__name">Alex Carter</p>
      <p class="contact__role">CEO/Founder</p>
      <p class="contact__line">604-555-0193</p>
      <p class="contact__line">info@brightwavereach.ca</p>
      <p class="contact__line">www.brightwavereach.ca</p>
      <ul class="socials">
        <li class="socials__item"><span class="socials__dot"></span>Chatterly</li>
        <li class="socials__item"><span class="socials__dot"></span>Pixlora</li>
        <li class="socials__item"><span class="socials__dot"></span>Quibber</li>
      </ul>
    </div>
    <div class="leaf-art" role="img" aria-label="Large distressed dark grey maple leaf illustration">
      <span class="leaf-art__stripe" aria-hidden="true"></span>
    </div>
  </section>
</main>
</body>
</html>
```